Newsletter Ad

I am looking for someone to design an advertisement for a mother's club newsletter. 4" wide X by 5" tall (and 2.5" wide X 5" tall if possible).

I'm a psychotherapist, so want the ad to look professional, but modern. I have a logo with my photo attached that can be incorporated into the design. The colors of my website are turquoise and white. I'd like to keep with that theme...so maybe some turquoise blocking to match the logo font color.

I'm uploading a logo as well as an ad draft with the content I'd like listed in the ad.

```html
<!DOCTYPE html>
<html lang="en">
<head>
<meta charset="utf-8">
<title>Dana Morrell, MA, MFT – Newsletter Ad</title>
<link href="https://fonts.googleapis.com/css2?family=Didact+Gothic&display=swap" rel="stylesheet">
<style>
  :root {
    --turquoise: #26b8b9;
    --turquoise-deep: #2a9b9d;
    --ink: #222222;
    --white: #ffffff;
    --photo-dark: #2a2622;
    --photo-warm: #8a6e54;
  }
  * { margin: 0; padding: 0; box-sizing: border-box; }
  html, body { width: 960px; height: 1200px; overflow: hidden; background: var(--white); }
  body { font-family: "Didact Gothic", "Century Gothic", sans-serif; color: var(--ink); }
  .ad { position: relative; width: 960px; height: 1200px; background: var(--white); overflow: hidden; }

  .portrait {
    position: absolute; left: 36px; top: 102px; width: 170px; height: 214px;
    background: radial-gradient(ellipse at 55% 45%, var(--photo-warm) 0%, #5c4a3a 45%, var(--photo-dark) 80%);
  }
  .therapist-name {
    position: absolute; left: 238px; top: 116px;
    font-size: 57px; font-weight: 400; letter-spacing: -1.5px;
    color: var(--turquoise-deep); line-height: 1; white-space: nowrap;
  }
  .tagline {
    position: absolute; left: 240px; width: 565px; top: 226px;
    text-align: center; font-size: 39px; line-height: 47px; color: var(--ink);
  }

  .specialties {
    position: absolute; left: 0; top: 357px; width: 960px; height: 569px;
    background: var(--turquoise);
  }
  .specialties ul {
    list-style: none; padding-top: 44px; text-align: center;
    color: var(--white); font-size: 40px; line-height: 60px;
  }

  .contact {
    position: absolute; left: 0; top: 932px; width: 960px;
    text-align: center; color: var(--ink); font-style: normal;
  }
  .contact .address { font-size: 41px; line-height: 52px; letter-spacing: -0.5px; }
  .contact .line { font-size: 33px; line-height: 47px; }

  .license-bar {
    position: absolute; left: 0; top: 1130px; width: 960px; height: 70px;
    background: var(--turquoise);
  }
  .license {
    position: absolute; right: 28px; top: 0; line-height: 52px;
    font-size: 28px; letter-spacing: -0.5px; color: var(--white);
  }
</style>
</head>
<body>
  <main class="ad">
    <div class="portrait" role="img" aria-label="Portrait photograph of the therapist"></div>
    <h1 class="therapist-name">DANA MORRELL, MA, MFT</h1>
    <p class="tagline">Psychotherapy for<br>Individuals, Couples and Families</p>

    <section class="specialties">
      <ul>
        <li>Parenting</li>
        <li>Depression</li>
        <li>Anxiety</li>
        <li>Life Transitions</li>
        <li>Divorce</li>
        <li>Couples Issues</li>
        <li>Women’s Issues</li>
        <li>Attachment and Neuroscience</li>
      </ul>
    </section>

    <address class="contact">
      <p class="address">418 Alder Street, Fairbrook, CA 94960</p>
      <p class="line">www.danamorrell.com</p>
      <p class="line">dana@danamorrell.com</p>
      <p class="line">415.555.0148</p>
    </address>

    <footer class="license-bar">
      <p class="license">License# MFC48203</p>
    </footer>
  </main>
</body>
</html>
```